Environmental Consultancey needs Web Design

A consultancey firm based in Papua New Guinea specialising servicing a client market primarily in Melanesia, the wider Pacific Region and South East Asia. The firm provides services to community development and resource extraction activites that incorporate sustainable livelihoods for local customary land owners with environmentally responsibile practices and a focus on maintaining biodiversity and ecosystem services. We aim to encompass Culture, Custom and Science in our approach. Our website preferentially will convey a relaxed Pacific Island feel in its colours and design rather than a sterile corporate feel. See attached logo that will need to be visible on page or which may provide basis for ideas for the page.

Target Market(s)

Our target market is primarily the oil, gas and mining industry, secondarily international donor and aid programs followed by government projects and not for profit programs. Services include:
1. Biodiversity and Conservation - Fauna and Flora survey, assessment, management, monitoring & research, protected areas & endangered & threatend species.
2. Social & Community - impact, stakeholder engagement, census and survey, land and community affairs, capacity building empowerment.
3. Environmental Management - sustainable use, enterprise development & management, biodiversity offsets.

Industry/Entity Type

Community

Requirements
Must have
• Multiple pages, Logo somewhere on home page. Space for a couple of photos that as yet ive not decieded upon.
Nice to have
• Perhaps incorporate shapes, texture and colours that convey a feel of the attached photo of a blue bird of paradise. The blue fine overlapping and interlocking feather patterns are appealing perhaps as a background and the other colours used in boarders ? Abstract is fine as would be symbolic images or tribal ambience. The company is all about blending humanity in all its forms with the environment.

```html
<!DOCTYPE html>
<html lang="en">
<head>
<meta charset="utf-8">
<title>Tidewater Ecology</title>
<link rel="stylesheet" href="https://fonts.googleapis.com/css2?family=Source+Sans+3:wght@400;600;700&display=swap">
<style>
  :root {
    --bar-top: #40d6f3;
    --bar-bottom: #1a8ea9;
    --ink: #2a2a2a;
    --body-text: #4a4a4a;
    --link: #17809c;
    --page: #ffffff;
    --frame: #dcdcdc;
    --dot: #8a9aa0;
  }
  * { box-sizing: border-box; margin: 0; padding: 0; }
  html, body { width: 1117px; height: 1200px; overflow: hidden; background: var(--page); }
  body { position: relative; font-family: "Source Sans 3", sans-serif; color: var(--body-text); }

  .nav-bar {
    position: absolute; left: 24px; top: 49px; width: 1069px; height: 35px;
    border-radius: 12px;
    background: linear-gradient(var(--bar-top), var(--bar-bottom));
  }
  .nav-list { position: absolute; left: 487px; top: 0; height: 35px; display: flex; list-style: none; }
  .nav-list li {
    height: 35px; line-height: 35px; color: #fff; font-size: 15px; text-align: center;
    border-left: 1px solid rgba(255,255,255,0.45);
  }
  .nav-list li:nth-child(1) { width: 92px; }
  .nav-list li:nth-child(2) { width: 115px; }
  .nav-list li:nth-child(3) { width: 145px; }
  .nav-list li:nth-child(4) { width: 110px; }
  .nav-list li:nth-child(5) { width: 143px; }

  .brand {
    position: absolute; left: 42px; top: 4px; width: 138px; height: 138px; border-radius: 50%;
    background: var(--page); display: flex; align-items: center; justify-content: center;
    text-align: center; font-size: 16px; font-weight: 700; color: var(--bar-bottom); line-height: 1.15;
  }

  .hero-photo {
    position: absolute; left: 24px; top: 101px; width: 715px; height: 329px;
    background: radial-gradient(ellipse at 40% 45%, #3d7fd0 0%, #2a67b4 30%, #2f8a7a 65%, #4f9a6a 100%);
  }
  .hero-copy { position: absolute; left: 775px; top: 121px; width: 290px; }
  .hero-title { font-size: 32px; font-weight: 700; color: var(--ink); line-height: 39px; letter-spacing: 0.5px; }
  .hero-text { margin-top: 8px; padding-left: 4px; font-size: 14px; line-height: 21px; }
  .slider-dots { position: absolute; left: 891px; top: 409px; display: flex; gap: 6px; }
  .slider-dots span { width: 10px; height: 10px; border-radius: 50%; background: var(--dot); }

  .section-title { font-size: 30px; font-weight: 400; color: var(--ink); line-height: 36px; }
  .body-copy { font-size: 14px; line-height: 23px; }
  .more-link { position: absolute; font-size: 14px; color: var(--link); }

  .welcome { position: absolute; left: 24px; top: 448px; width: 594px; }
  .welcome .body-copy { margin-top: 6px; }
  .news { position: absolute; left: 695px; top: 451px; width: 400px; }
  .news .section-title { font-size: 28px; }
  .news-date { margin-top: 10px; padding-left: 2px; font-size: 16px; font-weight: 700; color: #3a3a3a; }
  .news .body-copy { line-height: 18.5px; margin-top: 4px; }

  .projects-title { position: absolute; left: 24px; top: 679px; }
  .story-title { position: absolute; left: 657px; top: 679px; }

  .photo-frame {
    position: absolute; background: var(--page); border: 1px solid var(--frame);
    box-shadow: 0 1px 3px rgba(0,0,0,0.18); padding: 4px;
  }
  .photo-frame .fill { width: 100%; height: 100%; }
  .thumb { width: 159px; height: 153px; }

  .story-copy { position: absolute; left: 673px; top: 911px; width: 400px; }
  .story-copy .lead { font-size: 15px; line-height: 23px; }
  .story-copy .note { margin-top: 26px; font-size: 13px; line-height: 23px; }

  .site-footer {
    position: absolute; left: 24px; top: 1121px; width: 1069px; height: 79px;
    background: linear-gradient(var(--bar-top), var(--bar-bottom));
    color: #fff; font-size: 12px; line-height: 19px; text-align: center; padding-top: 23px;
  }
</style>
</head>
<body>
  <header>
    <div class="nav-bar">
      <ul class="nav-list">
        <li>Home</li><li>About us</li><li>Our Activities</li><li>Services</li><li>Contact us</li>
      </ul>
    </div>
    <div class="brand">Tidewater<br>Ecology</div>
  </header>

  <section>
    <div class="hero-photo" role="img" aria-label="Photo of a blue bird of paradise among green foliage"></div>
    <div class="hero-copy">
      <h1 class="hero-title">Encompassing<br>Culture, Custom<br>&amp; Science</h1>
      <p class="hero-text">Lorem Ipsum is simply dummy text of the printing and typesetting industry. Lorem Ipsum has been the industry's standard dummy text ever since the 1500s, when an unknown printer took a galley of type and scrambled it to make a type specimen book.</p>
    </div>
    <div class="slider-dots"><span></span><span></span><span></span></div>
  </section>

  <section class="welcome">
    <h2 class="section-title">Welcome</h2>
    <p class="body-copy">Lorem Ipsum is simply dummy text of the printing and typesetting industry. Lorem Ipsum has been the industry's standard dummy text ever since the 1500s, when an unknown printer took a galley of type and scrambled it to make a type specimen book. Ipsum has been the industry's standard dummy text ever since the 1500s, when an unknown printer took a galley of type and scrambled it to make a type specimen book. Ipsum has been the industry's</p>
  </section>
  <a class="more-link" style="left:564px; top:634px;">view all</a>

  <section class="news">
    <h2 class="section-title">Latest News</h2>
    <p class="news-date">05 - 12 - 12</p>
    <p class="body-copy">Lorem Ipsum is simply dummy text of the printing and type-setting industry. Lorem Ipsum has been the industry's standard dummy text ever since the 1500s, when an unknown printer took a galley of type and scrambled it to make a type specimen book.</p>
  </section>
  <a class="more-link" style="left:697px; top:634px;">view all news</a>

  <h2 class="section-title projects-title">Our Projects</h2>
  <div class="photo-frame thumb" style="left:42px; top:731px;"><div class="fill" role="img" aria-label="Photo of a lone green tree under a blue sky" style="background:linear-gradient(#8fb6dc 0%,#3f7a2a 45%,#4f8f2e 100%);"></div></div>
  <div class="photo-frame thumb" style="left:238px; top:731px;"><div class="fill" role="img" aria-label="Photo of an autumn tree on a lawn" style="background:linear-gradient(#a9b23e,#6f8a2c);"></div></div>
  <div class="photo-frame thumb" style="left:436px; top:731px;"><div class="fill" role="img" aria-label="Photo of a seedling held in a hand" style="background:radial-gradient(circle at 50% 55%,#3f5a20,#6fa12e 60%,#8cbd3a);"></div></div>
  <div class="photo-frame thumb" style="left:42px; top:934px;"><div class="fill" role="img" aria-label="Photo of a leaf on rippling water" style="background:radial-gradient(circle at 50% 60%,#a9c93a,#6c9a1e 70%);"></div></div>
  <div class="photo-frame thumb" style="left:238px; top:934px;"><div class="fill" role="img" aria-label="Photo of a butterfly on a yellow flower" style="background:linear-gradient(135deg,#5aa13a,#3d8a2a 60%,#e8b030);"></div></div>
  <div class="photo-frame thumb" style="left:436px; top:934px;"><div class="fill" role="img" aria-label="Photo of a glass globe among leaves" style="background:radial-gradient(circle at 50% 40%,#e4efd6,#9dbf7c 55%,#3f7a2a);"></div></div>

  <h2 class="section-title story-title">Our Story</h2>
  <div class="photo-frame" style="left:662px; top:731px; width:430px; height:153px;"><div class="fill" role="img" aria-label="Photo of a bird of paradise displaying its plumes" style="background:linear-gradient(90deg,#2f5a3a,#6f8f4a 50%,#b5b070);"></div></div>
  <div class="story-copy">
    <p class="lead">Lorem Ipsum is simply dummy text of the printing and typesetting industry. Lorem Ipsum has been the indus-try's standard dummy text ever since the 1500s,</p>
    <p class="note">when an unknown printer took a galley of type and scrambled it to make a type specimen book.</p>
  </div>
  <a class="more-link" style="left:1039px; top:1069px;">view all</a>

  <footer class="site-footer">
    <p>© 2012 Tidewater Ecology</p>
    <p>Terms of Service - Privacy Policy - Program Policies</p>
  </footer>
</body>
</html>
```